Website for Architecture & Interior Design firm

We are architecture and interior design firm looking for website design, word press based, smooth, elegant and easy to use for visitors. It should be easy to navigate using a mobile phone, with the ability to change pictures easily. It is a Bilingual website, (English: left to right, Arabic: right to left). A button in the menu bar is required to change the language, At first, we expect an English version, then we will help the designer by providing Arabic translation for any part of the website. Our website main purpose is to display our works in a picture format (Portfolio) to our clients, which mainly consist of four galleries from our (Services) as follow: 1- Architecture 2- Interior Design 3- Project Management 4- Importing from Abroad - Each service will have its page, which displays projects(items) in thumbnail format with simple text, which deploys (when clicked) into Fullscreen gallery to show the items related pictures (Dark gray or black background). - Navigation buttons/arrows are required, (X) button to close the navigation. - This is a very important part, the user experience in PC/Browser mode or Mobile mode should be easy, error-free and fast. Our homepage consists of four main elements: A- Edge to edge picture (Changing in a smooth transitional way, Random pictures from our Services) with our Logo, also persistent menu bar in the top (Home | About Us | Architecture | Interior design | Project Management | Importing from Abroad) + Social media icons B- Photo tiles (Random pictures from our Services) C- Our Services in a fixed 4-tile picture (Clickable) D- Contact Section (Simple name, contact number, message form) We expect the final service should be: 1- a fully functioning website, WordPress based, ready to be used by visitors 2- full content filling, we will contact the designer and provide the material (texture, text,etc..)
Colors
Designer to choose colors to be used in the design.
Look and feel
Each slider illustrates characteristics of the customer's brand and the style your logo design should communicate.

```html
<!DOCTYPE html>
<html lang="en">
<head>
<meta charset="utf-8">
<title>Arcline Design &amp; Project Management</title>
<link href="https://fonts.googleapis.com/css2?family=Archivo:wght@400;500;600;700;800&family=Lato:wght@400&display=swap" rel="stylesheet">
<style>
:root{
  --blue:#1f5fa8;
  --navy:#0f2444;
  --ink:#1a1a1a;
  --gold:#b8893a;
  --mist:#eef0f3;
  --line:#d6d9de;
}
*{box-sizing:border-box;margin:0;padding:0}
html,body{width:1200px;height:3349px;overflow:hidden;background:#fff}
body{font-family:"Archivo",Arial,sans-serif;color:var(--ink);position:relative}
.abs{position:absolute}

/* header */
.header{left:0;top:0;width:1200px;height:133px;background:#fff}
.brand-box{left:93px;top:0;width:228px;height:170px;background:#fff;box-shadow:0 2px 8px rgba(0,0,0,.18);z-index:5;display:flex;flex-direction:column;align-items:center;justify-content:center;gap:8px}
.brand-mark{width:34px;height:34px;background:var(--blue)}
.brand-name{font-family:"Archivo",sans-serif;font-weight:500;font-size:17px;color:var(--navy);text-align:center;line-height:1.25;letter-spacing:.5px}
.social{display:flex;gap:28px}
.social span{width:20px;height:20px;border-radius:50%;background:var(--blue);display:block}
.header .social{left:833px;top:26px}
.lang{left:1032px;top:19px;width:82px;height:35px;border:1px solid #9aa0a8;font-size:13px;display:flex;align-items:center;justify-content:center;gap:6px;color:#333}
.nav{left:342px;top:83px;display:flex;gap:27px;font-weight:700;font-size:14.5px;color:#111}
.nav a{color:inherit;text-decoration:none;padding-bottom:8px}
.nav a.active{color:var(--blue);border-bottom:2px solid var(--blue)}

/* hero */
.hero{left:0;top:133px;width:1200px;height:633px;background:radial-gradient(ellipse at 55% 30%,#4a4f86 0%,#2b2f5a 35%,#1a1c38 70%,#14152a 100%)}
.hero-photo{position:absolute;inset:0;background:linear-gradient(180deg,rgba(40,44,90,.2) 0%,rgba(120,80,60,.25) 55%,rgba(30,28,45,.4) 100%)}
.hero-kicker{left:0;width:1200px;top:265px;text-align:center;color:#fff;font-weight:400;font-size:44px;letter-spacing:-1px}
.hero-title{left:0;width:1200px;top:318px;text-align:center;color:#fff;font-weight:800;font-size:83px;letter-spacing:-1px}
.btn{background:var(--blue);color:#fff;font-weight:700;display:flex;align-items:center;justify-content:center}
.hero-btn{left:492px;top:420px;width:207px;height:52px;font-size:19px}
.wedge{left:0;top:650px;width:1200px;height:120px}

/* section heading */
.sec-title{left:0;width:1200px;text-align:center;font-weight:700;font-size:35px;color:var(--navy)}
.sec-rule{width:80px;height:4px;background:var(--navy)}

/* services */
.tile{top:852px;height:293px;display:flex;align-items:flex-end;justify-content:center;color:#fff;font-weight:700;font-size:22px;text-align:center}
.tile .cap{width:100%;padding:0 0 22px;background:linear-gradient(180deg,rgba(0,0,0,0),rgba(0,0,0,.45));line-height:1.25}
.tile-arch{left:0;width:295px;background:linear-gradient(160deg,#d9d2c4 0%,#8a95a6 45%,#3a6ab4 100%)}
.tile-int{left:303px;width:293px;background:linear-gradient(180deg,#6b5b3c 0%,#2e2a25 50%,#7a6a50 100%)}
.tile-pm{left:604px;width:293px;background:linear-gradient(160deg,#4b8bd0,#2565ab);align-items:center;flex-direction:column;justify-content:center;gap:16px;line-height:1.3}
.tile-pm .ghost{border:2px solid #fff;font-size:16px;padding:9px 28px}
.tile-imp{left:905px;width:295px;background:linear-gradient(180deg,#6b7490 0%,#c87a4a 45%,#3a2f2a 70%,#1d1d24 100%)}

/* about */
.about-mark{left:230px;top:1230px;width:260px;height:450px}
.about-title{left:585px;top:1276px;font-weight:700;font-size:36px;color:var(--navy)}
.about-rule{left:585px;top:1327px;width:80px;height:4px;background:var(--navy)}
.about-text{left:582px;top:1355px;width:520px;font-family:"Lato",sans-serif;font-size:17.5px;line-height:27px;color:#222}
.about-text p+p{margin-top:27px}
.about-btn{left:578px;top:1549px;width:186px;height:48px;font-size:18px}

/* gallery */
.gallery-title{color:var(--gold)}
.g{background:#ccc}

/* contact */
.contact{left:0;top:2393px;width:1200px;height:682px;background:linear-gradient(180deg,#f0f1f3,#e6e9ed)}
.contact-co{left:0;width:1200px;top:2559px;text-align:center;font-weight:600;font-size:20px;color:var(--navy)}
.contact-ph{left:0;width:1200px;top:2588px;text-align:center;font-weight:600;font-size:28px;color:var(--navy)}
.field{background:#fff;border:1px solid var(--line);box-shadow:0 1px 3px rgba(0,0,0,.08);font-size:18px;color:#333;padding:16px 20px 0}
.submit{left:505px;top:2938px;width:207px;height:53px;font-size:19px}

/* footer */
.foot-brand{left:150px;top:3118px;width:180px;height:140px;display:flex;flex-direction:column;align-items:center;justify-content:center;gap:10px}
.foot-col{font-weight:700;font-size:13.5px;color:#222;line-height:25.5px}
.foot-meta{left:875px;top:3221px;font-size:13px;color:#222;line-height:26px}
.foot-meta a{color:var(--navy);text-decoration:none}
</style>
</head>
<body>

<header class="abs header">
  <nav class="abs nav">
    <a class="active" href="#">ABOUT US</a>
    <a href="#">ARCHITECTURE</a>
    <a href="#">INTERIOR DESIGN</a>
    <a href="#">PROJECT MANAGEMENT</a>
    <a href="#">IMPORTING FROM ABROAD</a>
  </nav>
  <div class="abs social" aria-label="Social links"><span></span><span></span><span></span><span></span></div>
  <div class="abs lang">ENG
    <svg width="14" height="9" viewBox="0 0 14 9"><path d="M1 1l6 6 6-6" fill="none" stroke="#333" stroke-width="1.6"/></svg>
  </div>
</header>
<div class="abs brand-box">
  <span class="brand-mark"></span>
  <div class="brand-name">ARCLINE<br>DESIGN &amp; PROJECT<br>MANAGEMENT</div>
</div>

<section class="abs hero" role="img" aria-label="Night aerial view of a city skyline with illuminated towers">
  <div class="hero-photo"></div>
</section>
<svg class="abs" style="left:88px;top:350px" width="30" height="56" viewBox="0 0 30 56"><path d="M26 2L4 28l22 26" fill="none" stroke="rgba(255,255,255,.7)" stroke-width="2.5"/></svg>
<svg class="abs" style="left:1110px;top:350px" width="30" height="56" viewBox="0 0 30 56"><path d="M4 2l22 26L4 54" fill="none" stroke="rgba(255,255,255,.7)" stroke-width="2.5"/></svg>
<div class="abs hero-kicker">WELCOME TO</div>
<div class="abs hero-title">ARCLINE DESIGNS</div>
<div class="abs btn hero-btn">GET STARTED</div>

<svg class="abs wedge" viewBox="0 0 1200 120" preserveAspectRatio="none">
  <polygon points="0,120 0,118 600,10 1200,118 1200,120" fill="#fff"/>
  <polyline points="40,125 600,16 1160,120" fill="none" stroke="var(--blue)" stroke-width="4"/>
</svg>

<div class="abs" style="left:589px;top:697px;width:22px;height:48px;border:3px solid var(--blue)"></div>
<div class="abs sec-title" style="top:757px">OUR SERVICES</div>
<div class="abs sec-rule" style="left:558px;top:808px"></div>

<div class="abs tile tile-arch" role="img" aria-label="Modern building facade with geometric panels"><div class="cap">ARCHITECTURE</div></div>
<div class="abs tile tile-int" role="img" aria-label="Ornate arched interior hall"><div class="cap">INTERIOR DESIGN</div></div>
<div class="abs tile tile-pm" role="img" aria-label="Engineer on a construction site"><div>PROJECT<br>MANAGEMENT</div><div class="ghost">CLICK HERE</div></div>
<div class="abs tile tile-imp" role="img" aria-label="Container port with cranes at dusk"><div class="cap">IMPORTING FROM<br>ABROAD</div></div>

<svg class="abs about-mark" viewBox="0 0 260 450" aria-label="Arcline brand block">
  <rect x="10" y="10" width="240" height="430" fill="none" stroke="var(--blue)" stroke-width="12"/>
  <rect x="60" y="60" width="140" height="140" fill="var(--blue)" opacity=".15"/>
</svg>
<h2 class="abs about-title">ABOUT US</h2>
<div class="abs about-rule"></div>
<div class="abs about-text">
  <p>Fusce tellus Sed metus augue convallis et vehicula ut pulvinar eu ante Integer orci tellus tristique vitae consequat nec</p>
  <p>Aorta vel lectus Nulla sit amet enim Proin dui lectus cursus eu mattis laoreet viverra sit amet quam Curabitur vel dolor ultrices ipsum dictum tristique Praesent vitae lacus Ut velit e</p>
</div>
<div class="abs btn about-btn">LEARN MORE</div>

<div class="abs sec-title gallery-title" style="top:1731px">OUR GALLERY</div>
<div class="abs sec-rule" style="left:551px;top:1781px"></div>

<div class="abs g" style="left:0;top:1835px;width:388px;height:277px;background:linear-gradient(180deg,#9fb8cf 0%,#d8c6a4 55%,#6f7a5a 80%,#8a8a8a 100%)" role="img" aria-label="City street with palm trees and towers"></div>
<div class="abs g" style="left:396px;top:1835px;width:397px;height:277px;background:linear-gradient(150deg,#5a8ac0 0%,#3e6a6a 45%,#c9bca0 100%)" role="img" aria-label="Glass and steel lattice roof"></div>
<div class="abs g" style="left:803px;top:1835px;width:397px;height:277px;background:radial-gradient(circle at 42% 30%,#cfe3ee 0%,#c6b49a 35%,#6d645a 100%)" role="img" aria-label="Spiral interior atrium with skylight"></div>
<div class="abs g" style="left:0;top:2122px;width:388px;height:271px;background:linear-gradient(180deg,#7fb0dc 0%,#3f86b8 50%,#5d7a5a 85%,#888 100%)" role="img" aria-label="Blue glass office towers"></div>
<div class="abs g" style="left:398px;top:2122px;width:395px;height:271px;background:radial-gradient(ellipse at 50% 70%,#fff2d8 0%,#f0a040 35%,#d46a1c 80%)" role="img" aria-label="Orange arched corridor"></div>
<div class="abs g" style="left:803px;top:2122px;width:397px;height:271px;background:linear-gradient(180deg,#0f1e5a 0%,#1c2e6e 55%,#3a6b4a 80%,#c8b88a 100%)" role="img" aria-label="Mosque with minaret at night"></div>

<section class="abs contact" role="img" aria-label="Faded city skyline backdrop"></section>
<div class="abs sec-title" style="top:2463px">CONTACT US</div>
<div class="abs sec-rule" style="left:558px;top:2514px"></div>
<div class="abs contact-co">ARCLINE DESIGNS</div>
<div class="abs contact-ph">(685) 555 0172</div>

<div class="abs field" style="left:195px;top:2658px;width:392px;height:53px">Name</div>
<div class="abs field" style="left:604px;top:2658px;width:392px;height:53px">Phone Number</div>
<div class="abs field" style="left:195px;top:2725px;width:392px;height:53px">Email address</div>
<div class="abs field" style="left:604px;top:2725px;width:392px;height:53px">Subject</div>
<div class="abs field" style="left:195px;top:2796px;width:801px;height:120px">Message</div>
<div class="abs btn submit">SUBMIT NOW</div>

<footer>
  <div class="abs foot-brand">
    <span class="brand-mark"></span>
    <div class="brand-name">ARCLINE<br>DESIGN &amp; PROJECT<br>MANAGEMENT</div>
  </div>
  <div class="abs foot-col" style="left:421px;top:3163px">HOME<br>ABOUT US<br>ARCHITECTURE<br>INTERIOR DESIGN</div>
  <div class="abs foot-col" style="left:612px;top:3165px">PROJECT MANAGEMENT<br>IMPORTING FROM ABROAD<br>CONTACT US</div>
  <div class="abs social" style="left:875px;top:3165px"><span></span><span></span><span></span><span></span></div>
  <div class="abs foot-meta">© 2019 Company Name<br>All right reserved &nbsp;|&nbsp; <a href="#">Privacy Policy</a></div>
</footer>

</body>
</html>
```